Business card for Sports Apparel business

DOUBLE SIDED DESIGN
We need business cards for a new sports apparel business. We are developing a protective headband for soccer initially.
Torvalle is focused on designing and developing head protection products to reduce the likelihood of concussion when playing sports. Exploring and understanding medical insights, material science research, current and former players experiences and governing bodies guidelines has allowed Torvalle to develop the safety, style, form and function requirements of a suitable product to bring to market.
Target Market(s)
Mums buying kits for the sons and daughters. Amateur footballers.
Industry/Entity Type
Sporting Good
Contact Information for Business Card
Martin Ashworth - CEO
Mobile: +44 7431589027
Email: martin@torvalle.co.uk
Tel: 0208 5519372
Helena Pargeter - COO
Mob: +44 7385 640117
Email: helena@torvalle.co.uk
Tel: 0208 5519372
Duncan Farrow - CCO
Mob: +44 7564 293081
Email: duncan@torvalle.co.uk
Tel: 0208 5519372
Look and feel
Each slider illustrates characteristics of the customer's brand and the style your logo design should communicate.

```html
<!DOCTYPE html>
<html lang="en">
<head>
<meta charset="utf-8">
<title>Torvalle — Business Card</title>
<link rel="stylesheet" href="https://fonts.googleapis.com/css2?family=Montserrat:wght@400;500;700&display=swap">
<style>
  :root {
    --backdrop: #1b1b1c;
    --card: #262627;
    --card-edge: #2f2f30;
    --brand-blue: #1667ad;
    --ink-light: #f2f2f2;
    --ink-soft: #d8d8d8;
  }
  * { box-sizing: border-box; margin: 0; padding: 0; }
  html, body {
    width: 1200px; height: 900px; overflow: hidden;
    background: var(--backdrop);
    font-family: "Montserrat", Arial, sans-serif;
  }
  .canvas {
    position: relative; width: 1200px; height: 900px;
    display: flex; flex-direction: column; align-items: center; justify-content: center; gap: 44px;
  }
  .card {
    position: relative; width: 640px; height: 366px;
    background: linear-gradient(135deg, var(--card) 0%, var(--card-edge) 100%);
    border-bottom: 7px solid var(--brand-blue);
    box-shadow: 0 18px 40px rgba(0,0,0,0.55);
  }
  .wordmark {
    display: flex; align-items: center; gap: 14px;
    font-weight: 700; color: var(--ink-light);
    letter-spacing: 0.06em; text-transform: uppercase;
  }
  .wordmark-square { background: var(--brand-blue); flex: none; }
  .card-front { display: flex; align-items: center; justify-content: center; }
  .card-front .wordmark { font-size: 54px; }
  .card-front .wordmark-square { width: 34px; height: 34px; }

  .card-back { display: flex; align-items: center; padding: 0 40px 0 44px; }
  .card-back .wordmark { font-size: 32px; gap: 10px; width: 268px; }
  .card-back .wordmark-square { width: 20px; height: 20px; }
  .divider { width: 2px; height: 172px; background: var(--brand-blue); margin: 0 28px 0 14px; }
  .contact-block { color: var(--ink-light); }
  .person-name {
    color: var(--brand-blue); font-weight: 500; font-size: 20px;
    letter-spacing: 0.1em; text-transform: uppercase; line-height: 1.1;
  }
  .person-role { font-size: 15px; color: var(--ink-soft); margin: 4px 0 20px; letter-spacing: 0.04em; }
  .contact-list { list-style: none; }
  .contact-list li { display: flex; align-items: center; gap: 12px; font-size: 16px; line-height: 1.65; letter-spacing: 0.03em; }
  .contact-list svg { width: 14px; height: 14px; flex: none; }
</style>
</head>
<body>
<main class="canvas">
  <section class="card card-front" aria-label="Card front">
    <div class="wordmark"><span class="wordmark-square"></span>Torvalle</div>
  </section>

  <section class="card card-back" aria-label="Card back">
    <div class="wordmark"><span class="wordmark-square"></span>Torvalle</div>
    <div class="divider"></div>
    <div class="contact-block">
      <p class="person-name">Martin Ashworth</p>
      <p class="person-role">CEO</p>
      <ul class="contact-list">
        <li>
          <svg viewBox="0 0 16 16" aria-hidden="true"><path d="M4 1.5l2.2 3-1.4 1.6c.9 2 2.4 3.5 4.4 4.4l1.6-1.4 3 2.2-1.3 2.6C7.5 14 2 8.5 1.5 2.8z" fill="none" stroke="var(--brand-blue)" stroke-width="1.3"/></svg>
          0208 5519372
        </li>
        <li>
          <svg viewBox="0 0 16 16" aria-hidden="true"><rect x="4" y="1" width="8" height="14" rx="1.5" fill="none" stroke="var(--brand-blue)" stroke-width="1.3"/><line x1="7" y1="12.5" x2="9" y2="12.5" stroke="var(--brand-blue)" stroke-width="1.3"/></svg>
          +44 7431589027
        </li>
        <li>
          <svg viewBox="0 0 16 16" aria-hidden="true"><rect x="1" y="3.5" width="14" height="9" fill="none" stroke="var(--brand-blue)" stroke-width="1.3"/><path d="M1 3.5l7 5 7-5" fill="none" stroke="var(--brand-blue)" stroke-width="1.3"/></svg>
          martin@torvalle.co.uk
        </li>
        <li>
          <svg viewBox="0 0 16 16" aria-hidden="true"><circle cx="8" cy="8" r="6.5" fill="none" stroke="var(--brand-blue)" stroke-width="1.3"/><ellipse cx="8" cy="8" rx="2.8" ry="6.5" fill="none" stroke="var(--brand-blue)" stroke-width="1.1"/><line x1="1.5" y1="8" x2="14.5" y2="8" stroke="var(--brand-blue)" stroke-width="1.1"/></svg>
          www.torvalle.co.uk
        </li>
      </ul>
    </div>
  </section>
</main>
</body>
</html>
```